Redesign of business card for Cedar Ridge Mechanical

We are looking for a new design for our business cards for Cedar Ridge Mechanical. We are a plumbing & HVAC construction company, operating on the West Coast of Canada and USA. Logo attached.
Industry/Entity Type
Construction - Plumbing & HVAC
Contact Information for Business Card
Name, address, phone numbers, email, website address
Look and feel
Each slider illustrates characteristics of the customer's brand and the style your logo design should communicate.

```html
<!DOCTYPE html>
<html lang="en">
<head>
<meta charset="utf-8">
<title>Cedar Ridge Mechanical – Business Card</title>
<link href="https://fonts.googleapis.com/css2?family=Montserrat:wght@300;400;700&display=swap" rel="stylesheet">
<style>
  :root {
    --stage: #2a2a2a;
    --ink: #050505;
    --paper: #ffffff;
    --accent-grey: #9a9a9a;
    --soft-white: #f2f2f2;
  }
  * { margin: 0; padding: 0; box-sizing: border-box; }
  html, body {
    width: 1200px; height: 880px; overflow: hidden;
    background: var(--stage);
    font-family: "Montserrat", sans-serif;
  }
  .canvas { position: relative; width: 1200px; height: 880px; }

  .card {
    position: absolute;
    width: 600px; height: 343px;
    border-radius: 26px;
    overflow: hidden;
  }

  /* Front */
  .card-front {
    left: 60px; top: 90px;
    background: var(--ink);
    display: flex; align-items: center; justify-content: center;
  }
  .brand {
    display: flex; align-items: center; gap: 16px;
    color: var(--paper);
    font-weight: 700;
    letter-spacing: 0.06em;
    text-transform: uppercase;
  }
  .brand-square { width: 22px; height: 22px; background: currentColor; flex: none; }
  .card-front .brand-name { font-size: 30px; }

  /* Back */
  .card-back {
    left: 540px; top: 447px;
    background: var(--paper);
  }
  .card-back .wave { position: absolute; inset: 0; }
  .card-back .brand {
    position: absolute; right: 34px; top: 44px;
    color: var(--ink); gap: 10px;
  }
  .card-back .brand-square { width: 14px; height: 14px; }
  .card-back .brand-name { font-size: 17px; }

  .rule {
    position: absolute; height: 1px; background: var(--soft-white);
  }
  .rule-top { right: 30px; width: 300px; top: 150px; }
  .rule-mid { left: 40px; width: 230px; top: 250px; }

  .person { position: absolute; left: 40px; top: 198px; color: var(--paper); }
  .person-name { font-weight: 700; font-size: 21px; letter-spacing: 0.04em; }
  .person-role { font-weight: 300; font-size: 14px; margin-top: 2px; }

  .contact-list {
    position: absolute; left: 40px; top: 262px;
    list-style: none; color: var(--paper);
    font-weight: 300; font-size: 14px;
  }
  .contact-list li { display: flex; align-items: center; gap: 10px; height: 22px; }
  .contact-list svg { width: 13px; height: 13px; fill: var(--paper); flex: none; }

  .address {
    position: absolute; right: 34px; top: 176px;
    color: var(--paper); text-align: right;
    font-weight: 300; font-size: 14px; line-height: 1.5;
  }
</style>
</head>
<body>
<main class="canvas">

  <section class="card card-front" aria-label="Card front">
    <div class="brand">
      <span class="brand-square"></span>
      <span class="brand-name">Cedar Ridge Mechanical</span>
    </div>
  </section>

  <section class="card card-back" aria-label="Card back">
    <svg class="wave" viewBox="0 0 600 343" preserveAspectRatio="none" aria-hidden="true">
      <path fill="var(--accent-grey)" d="M20,180 C110,128 260,118 400,90 C500,70 570,44 600,14 L600,38 C570,66 500,92 400,112 C260,142 110,140 0,185 Z"/>
      <path fill="var(--ink)" d="M0,343 L0,185 C110,140 260,142 400,112 C500,92 570,66 600,38 L600,343 Z"/>
    </svg>

    <div class="brand">
      <span class="brand-square"></span>
      <span class="brand-name">Cedar Ridge Mechanical</span>
    </div>

    <div class="rule rule-top"></div>

    <p class="address">Your address, City<br>State, Zip 1234</p>

    <div class="person">
      <p class="person-name">DANIEL HAYES</p>
      <p class="person-role">Managing Director</p>
    </div>

    <div class="rule rule-mid"></div>

    <ul class="contact-list">
      <li>
        <svg viewBox="0 0 24 24" aria-hidden="true"><path d="M6.6 10.8a15 15 0 0 0 6.6 6.6l2.2-2.2a1 1 0 0 1 1-.25 11.4 11.4 0 0 0 3.6.57 1 1 0 0 1 1 1V20a1 1 0 0 1-1 1A17 17 0 0 1 3 4a1 1 0 0 1 1-1h3.5a1 1 0 0 1 1 1c0 1.25.2 2.45.57 3.6a1 1 0 0 1-.25 1z"/></svg>
        123 456 789
      </li>
      <li>
        <svg viewBox="0 0 24 24" aria-hidden="true"><path d="M2 5h20v14H2z M4 7v.5l8 5 8-5V7l-8 5z" fill-rule="evenodd"/></svg>
        info@yourgmail.com
      </li>
      <li>
        <svg viewBox="0 0 24 24" aria-hidden="true"><circle cx="12" cy="12" r="10"/></svg>
        www.yourwebsite.com
      </li>
    </ul>
  </section>

</main>
</body>
</html>
```